Single-sided business card for restaurant velmora with new logo made on this site

Business card options with new logo including restaurant name, address, phone number and website. This business card is single-sided only and will be presented at the hostess desk for clients to take. I would like to see options based on a cream card background, a white card background, a yellow card background and a burgundy colored background. It needs to be elegant and traditional.

Target Market(s)

local and international crowd

Industry/Entity Type

restaurant

Contact Information for Business Card

address, website and phone number

Font styles to use
Serif

Colors
EE7325
F08F49
F5BC92
FAE3D3
FDF4ED

Requirements
Must have
• new logo, address, phone number, website
Should not have
• more than three colors

```html
<!DOCTYPE html>
<html lang="es">
<head>
<meta charset="utf-8">
<title>Velmora — tarjeta de presentación</title>
<link href="https://fonts.googleapis.com/css2?family=Crimson+Text:wght@400;600&display=swap" rel="stylesheet">
<style>
  :root {
    --backdrop: #2b2b2c;
    --card-white: #f4f4f3;
    --card-burgundy: #3a1917;
    --gold: #e9a92b;
    --ink-brown: #3b1a17;
    --text-light: #f3ebe4;
    --leaf-light: #e3e3e2;
    --leaf-dark: #4a2320;
  }
  * { box-sizing: border-box; margin: 0; padding: 0; }
  html, body { width: 1200px; height: 900px; overflow: hidden; }
  body {
    background: var(--backdrop);
    font-family: "Crimson Text", Georgia, serif;
    position: relative;
  }
  .card {
    position: absolute;
    width: 580px;
    height: 330px;
    border-radius: 22px;
    overflow: hidden;
    box-shadow: 0 14px 30px rgba(0,0,0,.45);
  }
  .card--front { left: 70px; top: 70px; background: var(--card-white); }
  .card--back  { left: 550px; top: 500px; background: var(--card-burgundy); }

  .foliage {
    position: absolute;
    right: 0; top: 0;
    width: 60%; height: 100%;
  }
  .card--front .foliage {
    background: radial-gradient(ellipse at 75% 45%, var(--leaf-light) 0%, rgba(227,227,226,0) 70%);
  }
  .card--back .foliage {
    background: radial-gradient(ellipse at 70% 40%, var(--leaf-dark) 0%, rgba(74,35,32,0) 70%);
  }

  .brand-name {
    position: absolute;
    font-weight: 600;
    line-height: 1;
    white-space: nowrap;
  }
  .card--front .brand-name {
    left: 70px; top: 170px;
    font-size: 46px;
    letter-spacing: 7px;
    color: var(--ink-brown);
  }
  .card--back .brand-name {
    left: 40px; top: 148px;
    font-size: 34px;
    letter-spacing: 5px;
    color: var(--text-light);
  }

  .divider {
    position: absolute;
    left: 262px; top: 30px;
    width: 1px; height: 270px;
    background: linear-gradient(to bottom, rgba(243,235,228,0), rgba(243,235,228,.7), rgba(243,235,228,0));
  }

  .contact {
    position: absolute;
    left: 284px; top: 105px;
    list-style: none;
    color: var(--text-light);
    font-size: 16px;
    line-height: 1.3;
    white-space: nowrap;
  }
  .contact__item { display: flex; align-items: flex-start; gap: 9px; margin-bottom: 14px; }
  .contact__icon { width: 15px; height: 15px; flex: none; margin-top: 3px; }
</style>
</head>
<body>

  <section class="card card--front" aria-label="Frente de la tarjeta">
    <div class="foliage" role="img" aria-label="Hojas de agave decorativas en gris claro"></div>
    <span class="brand-name">VELMORA</span>
  </section>

  <section class="card card--back" aria-label="Reverso de la tarjeta">
    <div class="foliage" role="img" aria-label="Hojas de agave decorativas en tono vino oscuro"></div>
    <span class="brand-name">VELMORA</span>
    <div class="divider"></div>
    <ul class="contact">
      <li class="contact__item">
        <svg class="contact__icon" viewBox="0 0 24 24" fill="var(--gold)"><path d="M6.6 10.8a15.1 15.1 0 0 0 6.6 6.6l2.2-2.2a1 1 0 0 1 1-.25 11.4 11.4 0 0 0 3.6.57 1 1 0 0 1 1 1V20a1 1 0 0 1-1 1A17 17 0 0 1 3 4a1 1 0 0 1 1-1h3.5a1 1 0 0 1 1 1c0 1.25.2 2.45.57 3.6a1 1 0 0 1-.25 1z"/></svg>
        <span>555-210-4837</span>
      </li>
      <li class="contact__item">
        <svg class="contact__icon" viewBox="0 0 24 24" fill="none" stroke="var(--gold)" stroke-width="2"><circle cx="12" cy="12" r="9"/><path d="M3 12h18M12 3c3 3.5 3 14.5 0 18M12 3c-3 3.5-3 14.5 0 18"/></svg>
        <span>www.velmora.com.mx</span>
      </li>
      <li class="contact__item">
        <svg class="contact__icon" viewBox="0 0 24 24" fill="var(--gold)"><path d="M12 2a7 7 0 0 0-7 7c0 5 7 13 7 13s7-8 7-13a7 7 0 0 0-7-7zm0 9.5A2.5 2.5 0 1 1 12 6.5a2.5 2.5 0 0 1 0 5z"/></svg>
        <span>Orquídea 415<br>Bahías de Santa Luz, Oaxaca CP 70410</span>
      </li>
    </ul>
  </section>

</body>
</html>
```